Fresh Dwelling Tract Guide needs a new Landing Page

I like to get a landing page or website with 2-3 pages to help target home buyers who are looking to buy homes from builders such as TW Residences, Morvik, P.L. Fennick, etc. The landing page/website to be non-cluttered and be able to explain to home buyers that there are many benefits to include me as their buyer's agent when they buy a brand new home from any builders.
I may want to incorporate a short explanation video (animated) on the landing page and then for the viewer to click on a button that will take them to another page where they can search for new homes from different builders.
Target Market(s)
Home buyers looking to buy brand new home from builders such as TW Residences, Morvik, P.L. Fennick, etc.
Industry/Entity Type
Real Estate
Number of Pages Required
2 page
Font styles to use
Requirements
Must have
- The landing page may have the explanation video at the bottom of the landing page (scrolled down) or there may be a CALL TO ACTION button that takes the viewer to the 2nd page to watch the explanation video. Once they watched the explanation video and are still interested, they can click on another CALL TO ACTION button that will take them to another website that they will be able to search for all the available new homes and register their contact information.
Should not have
- No clutters and no dark colors.

```html
<!DOCTYPE html>
<html lang="en">
<head>
<meta charset="UTF-8">
<title>Streetside House Walk</title>
<link rel="stylesheet" href="https://fonts.googleapis.com/css2?family=Poppins:wght@300;500;600;700&display=swap">
<style>
  :root {
    --white: #ffffff;
    --button-blue: #183a8c;
    --footer-brown: #5a4229;
    --photo-light: #c9ccd6;
    --photo-mid: #9fa3b2;
    --photo-warm: #8f7a66;
    --photo-shade: rgba(60, 62, 78, 0.38);
  }
  * { margin: 0; padding: 0; box-sizing: border-box; }
  html, body { width: 1200px; height: 724px; overflow: hidden; }
  body { font-family: 'Poppins', sans-serif; color: var(--white); position: relative; }

  .hero {
    position: absolute; left: 0; top: 0; width: 1200px; height: 669px; overflow: hidden;
  }
  .hero-photo {
    position: absolute; inset: 0;
    background:
      linear-gradient(180deg, var(--photo-light) 0%, var(--photo-mid) 45%, var(--photo-warm) 78%, var(--photo-mid) 100%);
  }
  .hero-photo::after {
    content: ""; position: absolute; inset: 0; background: var(--photo-shade);
  }

  .brand {
    position: absolute; left: 96px; top: 72px;
    display: flex; align-items: center; gap: 10px;
    font-weight: 500; font-size: 22px; letter-spacing: 0.3px;
  }
  .brand-dot { width: 14px; height: 14px; border-radius: 50%; background: var(--white); }

  .menu-toggle { position: absolute; left: 1033px; top: 53px; width: 20px; height: 18px; }

  .hero-copy {
    position: absolute; left: 0; top: 240px; width: 1200px; text-align: center;
  }
  .hero-kicker { font-weight: 300; font-size: 42px; line-height: 1.1; }
  .hero-title { font-weight: 700; font-size: 62px; line-height: 1.3; margin-top: 4px; letter-spacing: -0.3px; }
  .watch-video {
    display: inline-flex; align-items: center; gap: 10px;
    font-weight: 500; font-size: 26px; margin-top: 6px;
  }
  .cta {
    display: inline-flex; align-items: center; justify-content: center;
    width: 290px; height: 66px; border-radius: 33px;
    background: var(--button-blue); color: var(--white);
    font-weight: 600; font-size: 16px; letter-spacing: 0.2px;
    margin-top: 24px; text-decoration: none;
  }

  .slider-dots {
    position: absolute; left: 0; top: 624px; width: 1200px;
    display: flex; justify-content: center; align-items: center; gap: 11px;
  }
  .slider-dot { width: 9px; height: 9px; border-radius: 50%; background: var(--white); }
  .slider-dot.is-active { box-shadow: 0 0 0 3px rgba(0,0,0,0.15), 0 0 0 5px var(--white); width: 8px; height: 8px; }

  .site-footer {
    position: absolute; left: 0; top: 669px; width: 1200px; height: 55px;
    background: var(--footer-brown);
    display: flex; align-items: center; justify-content: center;
    font-weight: 500; font-size: 13px; letter-spacing: 0.2px;
  }
</style>
</head>
<body>
  <section class="hero">
    <div class="hero-photo" role="img" aria-label="Bright open-plan living and dining room with wooden table, chairs, sofa and pendant lights"></div>

    <div class="brand"><span class="brand-dot"></span>Streetside House Walk</div>

    <svg class="menu-toggle" viewBox="0 0 20 18" aria-label="Menu">
      <rect x="0" y="0" width="20" height="3.5" fill="#fff"/>
      <rect x="0" y="7.25" width="20" height="3.5" fill="#fff"/>
      <rect x="0" y="14.5" width="20" height="3.5" fill="#fff"/>
    </svg>

    <div class="hero-copy">
      <p class="hero-kicker">Welcome to</p>
      <h1 class="hero-title">Streetside House Walk</h1>
      <div class="watch-video">
        <svg width="26" height="26" viewBox="0 0 26 26" aria-hidden="true">
          <circle cx="13" cy="13" r="13" fill="#fff"/>
          <path d="M10 7.5 L19 13 L10 18.5 Z" fill="#7c7f8e"/>
        </svg>
        Watch Video
      </div>
      <br>
      <a class="cta" href="#">FIND YOUR DREAM HOUSE</a>
    </div>

    <div class="slider-dots">
      <span class="slider-dot is-active"></span>
      <span class="slider-dot"></span>
      <span class="slider-dot"></span>
      <span class="slider-dot"></span>
    </div>
  </section>

  <footer class="site-footer">Copyright © 2018. All Rights Reserved.</footer>
</body>
</html>
```